8x8 Social Media Ad - Brant Summit Expo

Attention Real Estate Agents
Please join us for our
Quarterly Real Estate Training Expo
The 2nd Saturday of February, May, August and November
Our Next Training Expo is _________________________________
From 9 am to 1 pm
at
Halvorne Suites Millbrook Court
4817 Copper Willow Lane, Dunmere, MD 20588
Scheduled Speakers
9:00 am - Marcus Pellington - Orientation
9:30 am - Derrin Oakfield - Multiple Income Streams / Crest Program
10:00 am - Talia Brennick - Marketing though Social Media
10:45 am - Rex Dunmore - Generating Business through Ru-Plaza
11:30 am - Kemi Adeyoro - Real Estate Investing
12:15 pm - Gregor Tamsey - (Main Speaker) Training Topic TBA
For more information call Marcus Pellington at (240) 555-0183 or email mpellington@brantsummithomes.example

```html
<!DOCTYPE html>
<html lang="en">
<head>
<meta charset="utf-8">
<title>Brant Summit Expo – Quarterly Real Estate Training Expo</title>
<link rel="stylesheet" href="https://fonts.googleapis.com/css2?family=Bebas+Neue&family=Poppins:wght@400;500;600;700;800;900&display=swap">
<style>
  :root {
    --teal: #08959a;
    --teal-dark: #067c80;
    --ink: #161616;
    --night: #151515;
    --white: #ffffff;
    --ring: #6d6d6d;
    --mist-top: #f4f5f6;
    --mist-bottom: #d9dcdf;
  }
  * { box-sizing: border-box; margin: 0; padding: 0; }
  html, body { width: 1200px; height: 1200px; overflow: hidden; background: var(--white); }
  .ad {
    position: relative; width: 1200px; height: 1200px; overflow: hidden;
    background: var(--white); font-family: "Poppins", sans-serif; color: var(--ink);
  }
  .abs { position: absolute; }

  .brand { left: 59px; top: 108px; width: 340px; display: flex; align-items: center; gap: 14px; }
  .brand-mark { width: 26px; height: 26px; background: var(--teal); flex: none; }
  .brand-name { font-family: "Poppins", sans-serif; font-weight: 700; font-size: 30px; line-height: 1.15; color: var(--teal); }

  .headline { left: 440px; top: 48px; }

  .title-band { left: 0; top: 256px; width: 1200px; height: 136px; background: var(--teal); }

  .skyline { left: 0; top: 392px; width: 1200px; height: 397px;
    background: linear-gradient(180deg, var(--mist-top) 0%, #eceef0 45%, var(--mist-bottom) 100%); }

  .schedule { left: 0; top: 402px; width: 1200px; text-align: center; font-weight: 700; font-size: 45px; line-height: 50px; letter-spacing: -0.3px; }

  .next-expo { left: 82px; top: 513px; width: 1036px; height: 53px; border: 2px solid var(--teal); border-radius: 12px; background: var(--white); overflow: hidden; }
  .next-expo-label { position: absolute; left: 0; top: 0; width: 465px; height: 100%; background: var(--teal);
    color: var(--white); font-weight: 600; font-size: 31px; line-height: 49px; padding-left: 21px; border-radius: 0 12px 12px 0; white-space: nowrap; }

  .hours { left: 91px; top: 582px; font-family: "Bebas Neue", sans-serif; font-size: 66px; line-height: 60px; letter-spacing: 0.5px; white-space: nowrap; }
  .divider { left: 511px; top: 592px; width: 2px; height: 42px; background: var(--ink); }
  .pin { left: 535px; top: 589px; }
  .venue { left: 567px; top: 583px; white-space: nowrap; }
  .venue-name { font-weight: 700; font-size: 22.5px; line-height: 30px; letter-spacing: 0.2px; }
  .venue-address { font-weight: 400; font-size: 18.5px; line-height: 26px; }

  .speakers-frame { left: 0; top: 0; }
  .speakers-label { left: 404px; top: 677px; width: 377px; height: 33px; background: var(--night); border-radius: 0 0 10px 10px;
    color: var(--white); font-weight: 600; font-size: 19px; letter-spacing: 5px; text-align: center; line-height: 33px; }

  .lower { left: 0; top: 789px; width: 1200px; height: 411px; background: var(--night); }

  .portrait-ring { width: 160px; height: 160px; border-radius: 50%; background: var(--ring); display: flex; align-items: center; justify-content: center; }
  .portrait { width: 136px; height: 136px; border-radius: 50%; background: radial-gradient(circle at 50% 40%, #9a8f88 0%, #4c4a4c 60%, #2a2b2f 100%); }

  .sep { top: 813px; width: 0; height: 256px; border-left: 1px dashed #8a8a8a; }

  .slot { top: 877px; width: 184px; text-align: center; color: var(--white); }
  .slot-time { font-weight: 600; font-size: 17px; line-height: 24px; }
  .slot-name { margin-top: 4px; color: var(--teal); font-weight: 700; font-size: 21px; line-height: 25px; text-transform: uppercase; }
  .slot-role { font-weight: 400; font-size: 15px; line-height: 20px; }
  .slot-rule { width: 38px; height: 2px; background: var(--white); margin: 14px auto 18px; }
  .slot-topic { font-weight: 400; font-size: 15.5px; line-height: 20px; }

  .contact { left: 68px; top: 1089px; width: 1066px; height: 42px; border: 2px solid var(--teal); border-radius: 21px; }
  .contact-lead { position: absolute; left: 22px; top: 0; line-height: 38px; color: var(--white); font-size: 19.5px; font-weight: 400; white-space: nowrap; }
  .contact-pill { position: absolute; left: 460px; top: -2px; right: -2px; height: 42px; background: var(--teal); border-radius: 21px;
    display: flex; align-items: center; color: var(--white); font-weight: 600; white-space: nowrap; }
  .contact-phone { display: flex; align-items: center; gap: 6px; margin-left: 20px; font-size: 19px; flex: none; }
  .contact-email { display: flex; align-items: center; gap: 10px; margin-left: 24px; font-size: 15px; flex: none; }
</style>
</head>
<body>
<main class="ad">
  <div class="abs brand">
    <span class="brand-mark"></span>
    <span class="brand-name">Brant Summit<br>Realty Group</span>
  </div>

  <svg class="abs headline" width="720" height="190" viewBox="0 0 720 190">
    <text x="4" y="56" font-family="Poppins, sans-serif" font-weight="900" font-size="56" fill="var(--teal)" textLength="362" lengthAdjust="spacingAndGlyphs">ATTENTION</text>
    <text x="4" y="120" font-family="Poppins, sans-serif" font-weight="900" font-size="58" fill="var(--ink)" textLength="690" lengthAdjust="spacingAndGlyphs">REAL ESTATE AGENTS!</text>
    <text x="4" y="180" font-family="Poppins, sans-serif" font-weight="500" font-size="54" fill="var(--ink)" textLength="670" lengthAdjust="spacingAndGlyphs">PLEASE JOIN US FOR OUR</text>
  </svg>

  <div class="abs title-band"></div>
  <svg class="abs" style="left:0;top:256px" width="1200" height="136" viewBox="0 0 1200 136">
    <text x="59" y="100" font-family="'Bebas Neue', sans-serif" font-size="98" fill="var(--white)" stroke="var(--ink)" stroke-width="3" paint-order="stroke" textLength="1082" lengthAdjust="spacingAndGlyphs">QUARTERLY REAL ESTATE TRAINING EXPO</text>
  </svg>

  <div class="abs skyline" role="img" aria-label="Faded city skyline photograph behind the event details"></div>

  <h2 class="abs schedule">THE 2ND SATURDAY OF<br>FEBRUARY, MAY, AUGUST AND NOVEMBER</h2>

  <div class="abs next-expo"><div class="next-expo-label">Our Next Training Expo is</div></div>

  <div class="abs hours">FROM 9 AM TO 1 PM</div>
  <div class="abs divider"></div>
  <svg class="abs pin" width="18" height="26" viewBox="0 0 18 26">
    <path d="M9 1C4.6 1 1 4.5 1 8.9 1 14.8 9 25 9 25s8-10.2 8-16.1C17 4.5 13.4 1 9 1z" fill="var(--teal)"/>
    <circle cx="9" cy="9" r="3.4" fill="var(--white)"/>
  </svg>
  <div class="abs venue">
    <div class="venue-name">HALVORNE SUITES MILLBROOK COURT</div>
    <div class="venue-address">4817 Copper Willow Lane, Dunmere, MD 20588</div>
  </div>

  <div class="abs lower"></div>

  <svg class="abs speakers-frame" width="1200" height="740" viewBox="0 0 1200 740">
    <path d="M137 724 V687 Q137 677 147 677 H1047 Q1057 677 1057 687 V724" fill="none" stroke="var(--ink)" stroke-width="1.5"/>
  </svg>
  <div class="abs speakers-label">SCHEDULED SPEAKERS</div>

  <div class="abs portrait-ring" style="left:59px;top:710px"><div class="portrait" role="img" aria-label="Portrait photo of Marcus Pellington"></div></div>
  <div class="abs portrait-ring" style="left:242px;top:710px"><div class="portrait" role="img" aria-label="Portrait photo of Derrin Oakfield"></div></div>
  <div class="abs portrait-ring" style="left:428px;top:710px"><div class="portrait" role="img" aria-label="Portrait photo of Talia Brennick"></div></div>
  <div class="abs portrait-ring" style="left:613px;top:710px"><div class="portrait" role="img" aria-label="Portrait photo of Rex Dunmore"></div></div>
  <div class="abs portrait-ring" style="left:799px;top:710px"><div class="portrait" role="img" aria-label="Portrait photo of Kemi Adeyoro"></div></div>
  <div class="abs portrait-ring" style="left:977px;top:710px"><div class="portrait" role="img" aria-label="Portrait photo of Gregor Tamsey"></div></div>

  <div class="abs sep" style="left:231px"></div>
  <div class="abs sep" style="left:415px"></div>
  <div class="abs sep" style="left:601px"></div>
  <div class="abs sep" style="left:785px"></div>
  <div class="abs sep" style="left:967px"></div>

  <div class="abs slot" style="left:41px">
    <div class="slot-time">9:00 AM</div>
    <div class="slot-name">Marcus<br>Pellington</div>
    <div class="slot-rule"></div>
    <div class="slot-topic">Orientation</div>
  </div>
  <div class="abs slot" style="left:231px">
    <div class="slot-time">9:30 AM</div>
    <div class="slot-name">Derrin<br>Oakfield</div>
    <div class="slot-rule"></div>
    <div class="slot-topic">Multiple<br>Income<br>Streams / Crest<br>Program</div>
  </div>
  <div class="abs slot" style="left:410px">
    <div class="slot-time">10.00 AM</div>
    <div class="slot-name">Talia<br>Brennick</div>
    <div class="slot-rule"></div>
    <div class="slot-topic">Marketing<br>through Social<br>Media</div>
  </div>
  <div class="abs slot" style="left:599px">
    <div class="slot-time">10.45 AM</div>
    <div class="slot-name">Rex Dunmore</div>
    <div class="slot-rule" style="margin-top:16px;margin-bottom:36px"></div>
    <div class="slot-topic">Generating<br>Business through<br>Ru-Plaza</div>
  </div>
  <div class="abs slot" style="left:787px">
    <div class="slot-time">11:30 AM</div>
    <div class="slot-name">Kemi<br>Adeyoro</div>
    <div class="slot-rule"></div>
    <div class="slot-topic">Real Estate<br>Investing</div>
  </div>
  <div class="abs slot" style="left:966px">
    <div class="slot-time">12:15 PM</div>
    <div class="slot-name">Gregor<br>Tamsey</div>
    <div class="slot-role">(Main Speaker)</div>
    <div class="slot-rule" style="margin-top:12px;margin-bottom:14px"></div>
    <div class="slot-topic">Training<br>Topic TBA</div>
  </div>

  <div class="abs contact">
    <span class="contact-lead">For more information call Marcus Pellington</span>
    <div class="contact-pill">
      <span class="contact-phone">
        <svg width="16" height="16" viewBox="0 0 24 24"><path d="M6.6 10.8a15.1 15.1 0 0 0 6.6 6.6l2.2-2.2a1 1 0 0 1 1-.25 11.4 11.4 0 0 0 3.6.57 1 1 0 0 1 1 1V20a1 1 0 0 1-1 1A17 17 0 0 1 3 4a1 1 0 0 1 1-1h3.5a1 1 0 0 1 1 1c0 1.250.2 2.45.57 3.57a1 1 0 0 1-.25 1z" fill="var(--ink)"/></svg>
        (240) 555-0183
      </span>
      <span class="contact-email">
        <svg width="22" height="15" viewBox="0 0 22 15"><rect x="1" y="1" width="20" height="13" rx="1.5" fill="none" stroke="var(--ink)" stroke-width="2"/><path d="M1.5 1.8 11 8.5l9.5-6.7" fill="none" stroke="var(--ink)" stroke-width="2"/></svg>
        mpellington@brantsummithomes.example
      </span>
    </div>
  </div>
</main>
</body>
</html>
```